Vale Linebacker Needs a new website!

We need a four page website for a new company based in San Francisco. We help companies connect better with their clients, employees, and vendors by implementing collaborative technology.
Similar Websites
Mist Rangers - http://www.mistrangers.example/
Skyforthing - http://www.skyforthing.example/ - I don't like the the rotating window or the pictures of people. I like the icons used to go to the next pages.
Color Combos
Blues and Yellows - http://www.huepairings.example/palette-sets/96/HuePairing96.html
We prefer graphics over the actual pictures of people in the header. Pictures of people working together in the text is fine.
Web Page Layout
Index
Cloud Advisory Services
Email Everywhere
CRM Implementation
For detailed copy please see this link https://files.paperhold.example/a/widgetladyla.example/document/d/7KtmPzWqAeRbYcNvHsJgLdFxTuQoIeMnBvCxZaSdFgHj/edit
Industry/Entity Type
It Company

```html
<!DOCTYPE html>
<html lang="en">
<head>
<meta charset="utf-8">
<title>Vale Linebacker</title>
<link href="https://fonts.googleapis.com/css2?family=Open+Sans:wght@300;400;600;700&display=swap" rel="stylesheet">
<style>
:root{
  --blue:#1f6fc4;
  --blue-dark:#15539a;
  --blue-deep:#0e3f7a;
  --yellow:#f6b716;
  --ink:#3a3a3a;
  --muted:#8a8a8a;
  --light:#eeeeee;
  --line:#dcdcdc;
  --footer:#3b3b3b;
  --footer-dark:#2c2c2c;
  --white:#ffffff;
}
*{box-sizing:border-box;margin:0;padding:0}
html,body{width:736px;height:1200px;overflow:hidden}
body{font-family:"Open Sans",Arial,sans-serif;color:var(--ink);background:var(--white);font-size:7px;line-height:1.5}
.wrap{width:590px;margin:0 auto;position:relative}

.site-header{height:40px;background:var(--white)}
.site-header .wrap{display:flex;align-items:center;justify-content:space-between;height:40px}
.brand{display:flex;align-items:center;gap:6px;font-weight:700;font-size:14px;color:var(--blue)}
.brand-dot{width:14px;height:14px;border-radius:50%;background:var(--blue)}
.main-nav{display:flex;gap:14px;font-size:7px;color:var(--ink)}
.main-nav a{color:inherit;text-decoration:none;padding:12px 0}
.main-nav a.active{color:var(--blue);border-bottom:2px solid var(--blue)}

.hero{height:305px;background:linear-gradient(180deg,#1a5ead,#2b7dd0 60%,#1d66b8);position:relative;overflow:hidden}
.hero-art{position:absolute;right:0;top:0;width:430px;height:305px;background:radial-gradient(ellipse at 60% 45%,#8fc0ee 0%,#3f8ad6 45%,rgba(31,111,196,0) 75%)}
.hero-text{position:absolute;left:74px;top:70px;width:260px;color:var(--white)}
.hero-text h1{font-weight:400;font-size:17px;line-height:1.25;text-transform:uppercase}
.hero-text p{font-size:6.5px;margin-top:8px;opacity:.9}
.btn{display:inline-block;font-size:6.5px;color:var(--white);padding:5px 12px;border-radius:2px;text-decoration:none}
.btn-yellow{background:var(--yellow);margin-top:14px}
.btn-blue{background:var(--blue)}
.dots{position:absolute;left:74px;bottom:14px;display:flex;gap:4px}
.dots span{width:6px;height:6px;border-radius:50%;background:rgba(255,255,255,.5)}
.dots span.on{background:var(--yellow)}

.services{height:255px;background:var(--white)}
.services .wrap{display:flex;justify-content:space-between;padding-top:55px}
.service{width:160px;text-align:center}
.service-icon{width:44px;height:44px;border-radius:50%;border:1.5px solid var(--line);margin:0 auto 10px;display:flex;align-items:center;justify-content:center}
.service h3{font-size:9px;font-weight:600;color:var(--blue);margin-bottom:5px}
.service p{font-size:6px;color:var(--muted);margin-bottom:10px}
.service-rule{height:1px;background:var(--line);width:590px;margin:30px auto 0}

.welcome{height:295px;background:var(--light)}
.welcome .wrap{display:flex;justify-content:space-between;padding-top:30px}
.welcome-main{width:395px}
.welcome-top{display:flex;gap:12px}
.welcome-photos{width:150px;height:64px;background:linear-gradient(90deg,#c9b6a2,#9c8a78);border-radius:2px;flex:none;align-self:center}
.welcome-top h2{font-size:13px;font-weight:600;color:var(--ink);width:100px;line-height:1.25;margin-top:4px}
.welcome-top h2 em{color:var(--blue);font-style:italic}
.welcome-top .lead{font-size:6px;color:var(--muted);width:125px}
.welcome-main .body{font-size:6px;color:var(--muted);margin-top:22px}
.contact-box{width:172px;background:var(--blue);padding:10px 12px 12px}
.contact-box h3{color:var(--white);font-size:9px;font-weight:600;margin-bottom:8px;padding-bottom:4px;border-bottom:1px solid rgba(255,255,255,.3)}
.field{background:var(--white);height:13px;margin-bottom:5px;font-size:5.5px;color:var(--muted);padding:2px 5px}
.field.tall{height:34px}
.contact-box .submit{display:block;margin:4px 0 0 auto;background:var(--yellow);color:var(--white);font-size:6px;padding:3px 10px;width:max-content}

.what-we-do{height:200px;background:var(--white)}
.what-we-do .wrap{display:flex;gap:40px;padding-top:15px}
.wwd-art{width:120px;height:120px;background:linear-gradient(180deg,#d8d8d8,#a9a9a9);flex:none}
.wwd-text h2{font-size:14px;font-weight:600;margin-top:5px}
.wwd-text .lead{font-size:6px;color:var(--muted);width:330px;margin-top:3px}
.ticks{list-style:none;display:grid;grid-template-columns:160px 160px;gap:4px 0;margin-top:14px;font-size:6px;color:var(--muted)}
.ticks li{display:flex;align-items:center;gap:4px}

.site-footer{height:105px;background:var(--footer);color:#cfcfcf}
.site-footer .wrap{display:flex;gap:18px;padding-top:10px;height:88px}
.site-footer h4{font-size:8px;font-weight:400;color:var(--white);margin-bottom:4px}
.site-footer p{font-size:5.5px;line-height:1.5}
.blog{width:110px}
.blog .date{color:var(--white);font-weight:600}
.map{width:110px;height:60px;background:linear-gradient(135deg,#d9d3c0,#b8c7a8);flex:none}
.address{width:110px}
.touch{width:100px}
.socials{display:flex;gap:4px;margin-bottom:6px}
.socials span{width:10px;height:10px;border-radius:50%;background:#777}
.bottom-bar{height:17px;background:var(--footer-dark);font-size:5px;color:#aaa}
.bottom-bar .wrap{line-height:17px}
</style>
</head>
<body>
<header class="site-header">
  <div class="wrap">
    <div class="brand"><span class="brand-dot"></span>Vale Linebacker</div>
    <nav class="main-nav">
      <a class="active">Home</a><a>Offer</a><a>Cloud Advisory</a><a>Email Everywhere</a><a>About Us</a><a>Contact</a>
    </nav>
  </div>
</header>

<section class="hero">
  <div class="hero-art" role="img" aria-label="Illustration of a hand touching a cloud linked to devices and mail icons"></div>
  <div class="hero-text">
    <h1>Cloud Program<br>on the path to success</h1>
    <p>We connect your teams, clients and vendors through smart collaborative tools that keep work moving.</p>
    <a class="btn btn-yellow">Read More »</a>
  </div>
  <div class="dots"><span class="on"></span><span></span><span></span></div>
</section>

<section class="services">
  <div class="wrap">
    <div class="service">
      <div class="service-icon"><svg width="22" height="16" viewBox="0 0 22 16"><path d="M6 15h11a4 4 0 0 0 0-8 6 6 0 0 0-11-1 4.5 4.5 0 0 0 0 9z" fill="none" stroke="#1f6fc4" stroke-width="1.5"/></svg></div>
      <h3>Cloud Advisory Services</h3>
      <p>Forward-thinking organizations move to the cloud to work smarter, faster and together.</p>
      <a class="btn btn-blue">More »</a>
    </div>
    <div class="service">
      <div class="service-icon"><svg width="20" height="14" viewBox="0 0 20 14"><rect x="1" y="1" width="18" height="12" fill="none" stroke="#1f6fc4" stroke-width="1.5"/><path d="M1 1l9 7 9-7" fill="none" stroke="#1f6fc4" stroke-width="1.5"/></svg></div>
      <h3>Email Everywhere</h3>
      <p>Reach your inbox from any device with secure, always-on mail built for modern teams.</p>
      <a class="btn btn-blue">More »</a>
    </div>
    <div class="service">
      <div class="service-icon"><svg width="20" height="18" viewBox="0 0 20 18"><circle cx="10" cy="6" r="4" fill="none" stroke="#1f6fc4" stroke-width="1.5"/><path d="M2 17a8 6 0 0 1 16 0" fill="none" stroke="#1f6fc4" stroke-width="1.5"/></svg></div>
      <h3>CRM Implementation</h3>
      <p>Bring every client record together so your people sell and serve with full context.</p>
      <a class="btn btn-blue">More »</a>
    </div>
  </div>
  <div class="service-rule"></div>
</section>

<section class="welcome">
  <div class="wrap">
    <div class="welcome-main">
      <div class="welcome-top">
        <div class="welcome-photos" role="img" aria-label="Photos of two team members"></div>
        <h2>Welcome to Our Website <em>Mainpage..</em></h2>
        <p class="lead">We are a San Francisco team of cloud specialists helping companies connect better with clients, staff and vendors. Our goal is simple: tools people enjoy using every day.</p>
      </div>
      <p class="body">From first assessment to rollout and training, we plan, migrate and support collaborative technology that fits the way you already work. We measure success by adoption, lower costs and teams that share knowledge freely across every office and device.</p>
    </div>
    <form class="contact-box">
      <h3>Contact Us</h3>
      <div class="field">Enter Name</div>
      <div class="field">Enter Email</div>
      <div class="field">Enter Phone</div>
      <div class="field tall">Enter Message</div>
      <span class="submit">SUBMIT</span>
    </form>
  </div>
</section>

<section class="what-we-do">
  <div class="wrap">
    <div class="wwd-art" role="img" aria-label="Photo of a team working together"></div>
    <div class="wwd-text">
      <h2>What We Do</h2>
      <p class="lead">We make your work easier by providing unique insights, planning and proven tools your team can rely on. Our services include:</p>
      <ul class="ticks">
        <li><svg width="7" height="7" viewBox="0 0 7 7"><path d="M1 3.5l2 2 3-4" fill="none" stroke="#1f6fc4" stroke-width="1.2"/></svg>Strategy</li>
        <li><svg width="7" height="7" viewBox="0 0 7 7"><path d="M1 3.5l2 2 3-4" fill="none" stroke="#1f6fc4" stroke-width="1.2"/></svg>Integration</li>
        <li><svg width="7" height="7" viewBox="0 0 7 7"><path d="M1 3.5l2 2 3-4" fill="none" stroke="#1f6fc4" stroke-width="1.2"/></svg>Migration</li>
        <li><svg width="7" height="7" viewBox="0 0 7 7"><path d="M1 3.5l2 2 3-4" fill="none" stroke="#1f6fc4" stroke-width="1.2"/></svg>Adoption and change management</li>
        <li><svg width="7" height="7" viewBox="0 0 7 7"><path d="M1 3.5l2 2 3-4" fill="none" stroke="#1f6fc4" stroke-width="1.2"/></svg>Implementation</li>
      </ul>
    </div>
  </div>
</section>

<footer class="site-footer">
  <div class="wrap">
    <div class="blog">
      <h4>Latest Blog</h4>
      <p class="date">November 29, 2012</p>
      <p>Cloud teamwork explained simply</p>
      <p class="date">November 29, 2012</p>
      <p>Moving mail without the downtime</p>
    </div>
    <div class="map" role="img" aria-label="Map of the office location"></div>
    <div class="address">
      <h4>Contact Address</h4>
      <p>Vale Linebacker Ltd<br>Tel: +1 555 010 0199<br>Fax: +1 555 010 0198<br>hello@valelinebacker.example</p>
    </div>
    <div class="touch">
      <h4>Get in Touch</h4>
      <div class="socials"><span></span><span></span><span></span><span></span></div>
      <h4>Other Websites</h4>
      <p>Skyforthing · Mist Rangers<br>Hue Pairings</p>
    </div>
  </div>
  <div class="bottom-bar"><div class="wrap">© 2013 Vale Linebacker | Privacy Policy | Terms of Use</div></div>
</footer>
</body>
</html>
```